Meadowlark Property Review is a leading provider of residential appraisal and home inspection products in S

I need a business card/logo designed that obviously describes my business. We are a residential appraisal and home inspection company in Springfield, MO. We offer residential appraisals, home inspection, pest inspection and radon gas measurement. We have been in business for 18 years and hold state certified residential appraisal licenses and OBREX certified home inspection licenses. I have a logo that I really like and will attach, but would be open to new suggestions. I like more modern designs than traditional and would like a two sided card with our services, licenses and qualifications on the back.

```html
<!DOCTYPE html>
<html lang="en">
<head>
<meta charset="utf-8">
<title>Meadowlark Property Review – Business Card</title>
<link href="https://fonts.googleapis.com/css2?family=Open+Sans:wght@400;600;700&display=swap" rel="stylesheet">
<style>
  :root {
    --bg: #e9e6e1;
    --card: #ffffff;
    --gold: #f2b92c;
    --gold-deep: #e9a81c;
    --taupe: #a8946a;
    --brand: #8a7550;
    --ink: #2d2d2d;
    --rule: #222222;
  }
  * { margin: 0; padding: 0; box-sizing: border-box; }
  html, body {
    width: 1200px; height: 902px; overflow: hidden;
    background: var(--bg);
    font-family: "Open Sans", Arial, sans-serif;
    color: var(--ink);
  }
  .canvas { position: relative; width: 1200px; height: 902px; }

  .card {
    position: absolute;
    width: 540px; height: 309px;
    background: var(--card);
    box-shadow: 0 6px 18px rgba(0,0,0,0.18);
    overflow: hidden;
  }
  .card--front { left: 60px; top: 90px; }
  .card--back  { left: 600px; top: 500px; }

  .brand {
    position: absolute;
    display: flex; align-items: center; gap: 10px;
    color: var(--brand); font-weight: 700;
  }
  .brand__mark { width: 14px; height: 14px; background: var(--gold); flex: none; }
  .brand__name { font-size: 22px; line-height: 1.05; }
  .card--front .brand { left: 150px; top: 48px; }
  .card--back .brand { left: 40px; top: 125px; }
  .card--back .brand__name { font-size: 20px; }

  .services {
    position: absolute; list-style: none;
    font-size: 15px; line-height: 1.38;
  }
  .services li { display: flex; align-items: center; gap: 8px; }
  .services svg { width: 11px; height: 11px; flex: none; }
  .services--main { left: 46px; top: 150px; }
  .services--extra { left: 300px; top: 150px; }

  .bands { position: absolute; inset: 0; }

  .divider {
    position: absolute; left: 262px; top: 78px;
    width: 1.5px; height: 140px; background: var(--rule);
  }
  .contact {
    position: absolute; left: 280px; top: 82px;
    list-style: none; font-size: 13.5px; line-height: 1.45;
  }
  .contact li { display: flex; align-items: flex-start; gap: 8px; }
  .contact .icon { width: 13px; height: 13px; margin-top: 3px; flex: none; }
  .contact .address { display: block; }
</style>
</head>
<body>
<main class="canvas">

  <section class="card card--front" aria-label="Card front: services">
    <div class="brand">
      <span class="brand__mark"></span>
      <span class="brand__name">Meadowlark Property Review</span>
    </div>
    <ul class="services services--main">
      <li><svg viewBox="0 0 12 12"><path d="M1 6l3.5 4L11 1" fill="none" stroke="var(--gold)" stroke-width="2.4"/></svg>home inspection</li>
      <li><svg viewBox="0 0 12 12"><path d="M1 6l3.5 4L11 1" fill="none" stroke="var(--gold)" stroke-width="2.4"/></svg>property inspection</li>
      <li><svg viewBox="0 0 12 12"><path d="M1 6l3.5 4L11 1" fill="none" stroke="var(--gold)" stroke-width="2.4"/></svg>residential appraisal</li>
      <li><svg viewBox="0 0 12 12"><path d="M1 6l3.5 4L11 1" fill="none" stroke="var(--gold)" stroke-width="2.4"/></svg>termite inspection</li>
      <li><svg viewBox="0 0 12 12"><path d="M1 6l3.5 4L11 1" fill="none" stroke="var(--gold)" stroke-width="2.4"/></svg>radon gas measurement</li>
      <li><svg viewBox="0 0 12 12"><path d="M1 6l3.5 4L11 1" fill="none" stroke="var(--gold)" stroke-width="2.4"/></svg>pre purchase inspection</li>
    </ul>
    <ul class="services services--extra">
      <li><svg viewBox="0 0 12 12"><path d="M1 6l3.5 4L11 1" fill="none" stroke="var(--gold)" stroke-width="2.4"/></svg>thermal imaging</li>
      <li><svg viewBox="0 0 12 12"><path d="M1 6l3.5 4L11 1" fill="none" stroke="var(--gold)" stroke-width="2.4"/></svg>mechanical inspection</li>
      <li><svg viewBox="0 0 12 12"><path d="M1 6l3.5 4L11 1" fill="none" stroke="var(--gold)" stroke-width="2.4"/></svg>tax appeal</li>
      <li><svg viewBox="0 0 12 12"><path d="M1 6l3.5 4L11 1" fill="none" stroke="var(--gold)" stroke-width="2.4"/></svg>asset evaluation</li>
      <li><svg viewBox="0 0 12 12"><path d="M1 6l3.5 4L11 1" fill="none" stroke="var(--gold)" stroke-width="2.4"/></svg>energy audits</li>
    </ul>
  </section>

  <section class="card card--back" aria-label="Card back: contact details">
    <svg class="bands" viewBox="0 0 540 309" preserveAspectRatio="none" aria-hidden="true">
      <defs>
        <linearGradient id="goldBand" x1="0" y1="0" x2="1" y2="0">
          <stop offset="0" stop-color="var(--gold-deep)"/>
          <stop offset="1" stop-color="var(--gold)"/>
        </linearGradient>
      </defs>
      <polygon points="150,0 540,0 540,44 225,44 195,72 150,72" fill="url(#goldBand)"/>
      <polygon points="0,258 240,258 262,236 540,236 540,309 0,309" fill="var(--taupe)"/>
      <polygon points="240,309 262,262 400,262 400,309" fill="url(#goldBand)"/>
    </svg>

    <div class="brand">
      <span class="brand__mark"></span>
      <span class="brand__name">Meadowlark<br>Property Review</span>
    </div>

    <div class="divider"></div>

    <ul class="contact">
      <li><svg class="icon" viewBox="0 0 12 12"><rect x="1" y="1" width="10" height="10" rx="2" fill="var(--ink)"/><rect x="4" y="2.5" width="4" height="7" rx="0.8" fill="#fff"/></svg>417-555-0142</li>
      <li><svg class="icon" viewBox="0 0 12 12"><rect x="1" y="1" width="10" height="10" rx="2" fill="var(--ink)"/><path d="M4 3.2l1.2 1.6-.7.8c.4.9 1 1.5 1.9 1.9l.8-.7 1.6 1.2-.8 1C5.6 8.6 3.4 6.4 3 4z" fill="#fff"/></svg>417-555-0178</li>
      <li><svg class="icon" viewBox="0 0 12 12"><rect x="1" y="1" width="10" height="10" rx="2" fill="var(--ink)"/><rect x="3" y="4" width="6" height="5" fill="#fff"/><rect x="4" y="2.5" width="4" height="2" fill="#fff"/></svg>417-555-0193</li>
      <li><svg class="icon" viewBox="0 0 12 12"><rect x="1" y="1" width="10" height="10" rx="2" fill="var(--ink)"/><rect x="2.5" y="3.5" width="7" height="5" fill="#fff"/><path d="M2.5 3.5L6 6.5l3.5-3" fill="none" stroke="var(--ink)" stroke-width="0.8"/></svg>info@meadowlarkreview.com</li>
      <li><svg class="icon" viewBox="0 0 12 12"><rect x="1" y="1" width="10" height="10" rx="2" fill="var(--ink)"/><path d="M6 2.5a2.5 2.5 0 0 1 2.5 2.5C8.5 7 6 9.5 6 9.5S3.5 7 3.5 5A2.5 2.5 0 0 1 6 2.5z" fill="#fff"/></svg>
        <span class="address">Meadowlark Property Review<br>480 W Sunset Street; Suite C<br>Springfield, MO&nbsp; 65807</span>
      </li>
    </ul>
  </section>

</main>
</body>
</html>
```